Tolvik Commercial Cleaning is lookong for a new business card design.

A fresh new design that's professional and stylish. We need a serious upgrade to our business cards. I have included pictures of our existing ones. Our clients include professional individuals and business owners. We woupdblike something professional and upbeat. Please have fun and see what you come uo with.

Target Market(s)

Property managers, business owners, facility managers and other similar professionals

Industry/Entity Type

Janitorial

Contact Information for Business Card

Name, cell, office number, email, web address

Font styles to use
Sans Serif

Colors

Designer to choose colors to be used in the design.

Requirements
Must have
• please use the green color in our logo
Nice to have
• Bar code
Should not have
• Address

```html
<!DOCTYPE html>
<html lang="en">
<head>
<meta charset="UTF-8">
<title>Tolvik Commercial Cleaning – Business Card</title>
<link rel="stylesheet" href="https://fonts.googleapis.com/css2?family=Open+Sans:wght@400;700&display=swap">
<style>
  :root {
    --backdrop: #2b2f33;
    --card-white: #ffffff;
    --brand-green: #3bb75a;
    --brand-green-deep: #2c9446;
    --brand-blue: #3870ab;
    --ink: #111111;
  }
  * { margin: 0; padding: 0; box-sizing: border-box; }
  html, body { width: 1200px; height: 780px; overflow: hidden; }
  body {
    background: var(--backdrop);
    font-family: "Open Sans", Arial, sans-serif;
    display: flex;
    align-items: center;
    justify-content: center;
    gap: 60px;
  }
  .card {
    position: relative;
    width: 525px;
    height: 300px;
    border-radius: 18px;
    overflow: hidden;
  }

  /* Front */
  .card-front { background: var(--card-white); }
  .front-brand {
    position: absolute;
    left: 38px;
    top: 46px;
    width: 190px;
    color: var(--brand-green);
    font-weight: 700;
    line-height: 1.05;
  }
  .front-brand .brand-name { display: block; font-size: 50px; letter-spacing: -1px; }
  .front-brand .brand-line { display: block; font-size: 17px; margin-top: 4px; }
  .divider {
    position: absolute;
    left: 250px;
    top: 48px;
    width: 1.5px;
    height: 170px;
    background: var(--ink);
  }
  .contact {
    position: absolute;
    left: 272px;
    top: 92px;
  }
  .person-name {
    font-size: 24px;
    font-weight: 700;
    margin-bottom: 12px;
    white-space: nowrap;
  }
  .person-name .first { color: var(--brand-green); }
  .person-name .last { color: var(--brand-blue); }
  .contact-list { list-style: none; }
  .contact-list li {
    display: flex;
    align-items: center;
    gap: 7px;
    font-size: 14px;
    color: var(--ink);
    line-height: 1.55;
  }
  .contact-list svg { width: 12px; height: 12px; flex: none; }

  .bottom-band {
    position: absolute;
    left: 0;
    right: 0;
    bottom: 0;
    height: 26px;
    display: flex;
    align-items: flex-end;
  }
  .band-green { width: 190px; height: 16px; background: var(--brand-green); align-self: flex-start; }
  .band-mark {
    padding: 0 6px;
    color: var(--brand-green);
    font-weight: 700;
    font-size: 18px;
    line-height: 26px;
  }
  .band-blue { flex: 1; height: 16px; background: var(--brand-blue); }

  /* Back */
  .card-back {
    background: var(--brand-green);
    display: flex;
    flex-direction: column;
    align-items: center;
    justify-content: center;
    color: var(--brand-green-deep);
    font-weight: 700;
    text-align: center;
  }
  .card-back .brand-name { font-size: 86px; letter-spacing: -2px; line-height: 1; }
  .card-back .brand-line { font-size: 24px; margin-top: 8px; }
</style>
</head>
<body>

  <section class="card card-front" aria-label="Business card front">
    <div class="front-brand">
      <span class="brand-name">Tolvik</span>
      <span class="brand-line">commercial cleaning</span>
    </div>

    <div class="divider"></div>

    <div class="contact">
      <p class="person-name"><span class="first">Mara</span> <span class="last">Delling</span></p>
      <ul class="contact-list">
        <li>
          <svg viewBox="0 0 24 24" aria-hidden="true"><path fill="#3bb75a" d="M6.6 10.8a15.1 15.1 0 0 0 6.6 6.6l2.2-2.2a1 1 0 0 1 1-.25 11.4 11.4 0 0 0 3.6.57 1 1 0 0 1 1 1V20a1 1 0 0 1-1 1A17 17 0 0 1 3 4a1 1 0 0 1 1-1h3.5a1 1 0 0 1 1 1c0 1.25.2 2.45.57 3.57a1 1 0 0 1-.25 1z"/></svg>
          (555) 014-2867
        </li>
        <li>
          <svg viewBox="0 0 24 24" aria-hidden="true"><rect x="2" y="5" width="20" height="14" rx="2" fill="#3bb75a"/><path d="M3 6l9 7 9-7" fill="none" stroke="#fff" stroke-width="2"/></svg>
          mara@tolvikcleaning.com
        </li>
        <li>
          <svg viewBox="0 0 24 24" aria-hidden="true"><circle cx="12" cy="12" r="10" fill="#3bb75a"/><path d="M2 12h20M12 2c3 3 3 17 0 20M12 2c-3 3-3 17 0 20" fill="none" stroke="#fff" stroke-width="1.6"/></svg>
          www.tolvikcleaning.com
        </li>
      </ul>
    </div>

    <div class="bottom-band">
      <span class="band-green"></span>
      <span class="band-mark">Tolvik</span>
      <span class="band-blue"></span>
    </div>
  </section>

  <section class="card card-back" aria-label="Business card back">
    <span class="brand-name">Tolvik</span>
    <span class="brand-line">commercial cleaning</span>
  </section>

</body>
</html>
```